Medical Billing Company Needs a Business Card Design

We need a business card design for a Florida based medical billing company called 'Clinicians Keystone Solutions'. We specialize in providing revenue cycle management services to physician and therapist offices (we're basically their back-office processing partner for providing billing software, claims submissions, A/R follow-up and patient statements & collections. Our logo is red and blue-ish, so make sure that whatever other elements are used will match appropriately. Our current business card design has a too small font size. I'd like to project an image that shows we are modern & reliable. On a side note, I'm planning on using ZUB for printing these cards.

Target Market(s)

Office managers, physicians, therapists

Industry/Entity Type

Printing

Requirements
Must have
• Logo
Name of Employee
Phone
Fax
E-mail
Website

```html
<!DOCTYPE html>
<html lang="en">
<head>
<meta charset="utf-8">
<title>Clinicians Keystone Solutions – Business Card</title>
<link rel="stylesheet" href="https://fonts.googleapis.com/css2?family=Source+Sans+3:wght@400;600;700&display=swap">
<style>
  :root {
    --stage: #e6e6ea;
    --card-white: #ffffff;
    --navy: #2b2272;
    --purple: #4a3a95;
    --red: #a3161c;
    --red-light: #b8383d;
    --grey-text: #4a4a4a;
    --divider: #b9b9c2;
  }
  * { box-sizing: border-box; margin: 0; padding: 0; }
  html, body {
    width: 1200px; height: 987px; overflow: hidden;
    background: var(--stage);
    font-family: "Source Sans 3", Arial, sans-serif;
  }
  .stage { position: relative; width: 1200px; height: 987px; }

  .card {
    position: absolute;
    width: 560px; height: 320px;
    border-radius: 26px;
    overflow: hidden;
    box-shadow: 0 10px 24px rgba(0,0,0,0.18);
  }

  /* Back side */
  .card-back {
    left: 580px; top: 110px;
    background: radial-gradient(circle at 60% 35%, var(--red-light), var(--red) 75%);
    color: #fff;
  }
  .card-back .brand-name {
    position: absolute; left: 0; right: 0; top: 110px;
    text-align: center;
    font-size: 34px; font-weight: 600; letter-spacing: 2px;
  }
  .card-back .web {
    position: absolute; left: 0; right: 0; bottom: 70px;
    text-align: center;
    font-size: 18px; letter-spacing: 3px;
  }

  /* Front side */
  .card-front {
    left: 80px; top: 520px;
    background: var(--card-white);
  }
  .card-front .accent-area {
    position: absolute; left: 0; right: 0; bottom: 0;
    height: 78px;
    background: linear-gradient(180deg, var(--red) 0%, var(--purple) 70%);
  }
  .card-front .brand-name {
    position: absolute; left: 40px; top: 30px;
    font-size: 34px; font-weight: 600; letter-spacing: 1.5px;
    color: var(--navy); text-transform: uppercase;
  }
  .identity {
    position: absolute; right: 318px; top: 98px;
    text-align: right;
  }
  .identity .person { font-size: 22px; font-weight: 700; color: var(--purple); }
  .identity .title { font-size: 16px; color: var(--red); margin-bottom: 6px; }
  .identity .address { font-size: 15px; line-height: 1.25; color: var(--grey-text); }
  .divider {
    position: absolute; left: 256px; top: 104px;
    width: 1px; height: 92px; background: var(--divider);
  }
  .contacts {
    position: absolute; left: 272px; top: 104px;
    list-style: none;
    font-size: 17px; color: var(--grey-text); line-height: 23px;
  }
  .contacts li { display: flex; align-items: center; gap: 8px; }
  .contacts svg { width: 14px; height: 14px; flex: none; }
</style>
</head>
<body>
<main class="stage">

  <section class="card card-back" aria-label="Card back">
    <div class="brand-name">Clinicians Keystone</div>
    <div class="web">www.cliniciankeystone.com</div>
  </section>

  <section class="card card-front" aria-label="Card front">
    <div class="accent-area" role="img" aria-label="Decorative wave in red and purple"></div>

    <div class="brand-name">Clinicians Keystone</div>

    <div class="identity">
      <div class="person">Your Name</div>
      <div class="title">Title</div>
      <div class="address">Street Name, City Name<br>State Zip Code</div>
    </div>

    <div class="divider"></div>

    <ul class="contacts">
      <li>
        <svg viewBox="0 0 14 14" aria-hidden="true"><circle cx="7" cy="7" r="7" fill="var(--navy)"/><path d="M4.5 3.5l1.5 0 .7 2-1 .8a5 5 0 0 0 2 2l.8-1 2 .7 0 1.5c-3.5.5-6.5-2.5-6-6z" fill="#fff"/></svg>
        123-456-0789
      </li>
      <li>
        <svg viewBox="0 0 14 14" aria-hidden="true"><circle cx="7" cy="7" r="7" fill="var(--navy)"/><rect x="4" y="3.5" width="6" height="3" fill="#fff"/><rect x="3" y="6.5" width="8" height="4" rx="1" fill="#fff"/></svg>
        123-456-0789
      </li>
      <li>
        <svg viewBox="0 0 14 14" aria-hidden="true"><circle cx="7" cy="7" r="7" fill="var(--navy)"/><rect x="3" y="4.5" width="8" height="5.5" fill="#fff"/><path d="M3 4.5l4 3 4-3" fill="none" stroke="var(--navy)" stroke-width="0.8"/></svg>
        info@cliniciankeystone.com
      </li>
      <li>
        <svg viewBox="0 0 14 14" aria-hidden="true"><circle cx="7" cy="7" r="7" fill="var(--navy)"/><circle cx="7" cy="7" r="4" fill="none" stroke="#fff" stroke-width="0.9"/><path d="M3 7h8M7 3c-2 2-2 6 0 8M7 3c2 2 2 6 0 8" fill="none" stroke="#fff" stroke-width="0.8"/></svg>
        www.cliniciankeystone.com
      </li>
    </ul>
  </section>

</main>
</body>
</html>
```